KBT Business Cards

We require business cards for our business. We would like a matte black back to the card, with our logo centred in the middle. The front side of the card is open to design.

Target Market(s)

Clients looking for legal services (professional)

Industry/Entity Type

Legal

Contact Information for Business Card

Doran Kelbrath
Partner
Mobile: 0461 738 524
Email: doran@kbtlaw.co
Website: www.kbtlaw.co
Level 3, 118 Wendmore Street
Sydney NSW 2000

Font styles to use
Other font styles liked:
• Avenir

Colors
f04a50
ffffff
1b1b1b

Requirements
Must have
• Black back with logo included in the centre of the card.
• Our font is Avenir.

```html
<!DOCTYPE html>
<html lang="en">
<head>
<meta charset="utf-8">
<title>KBT Legal Business Cards</title>
<link href="https://fonts.googleapis.com/css2?family=Lato:wght@400;700;900&display=swap" rel="stylesheet">
<style>
  :root {
    --backdrop: #666666;
    --card-white: #ffffff;
    --card-black: #131213;
    --brand-red: #c0153a;
    --ink: #1b1b1b;
    --rule: #555555;
  }
  * { margin: 0; padding: 0; box-sizing: border-box; }
  html, body {
    width: 1200px; height: 900px; overflow: hidden;
    background: var(--backdrop);
    font-family: "Lato", "Avenir", sans-serif;
  }
  .stage { position: relative; width: 1200px; height: 900px; }
  .card {
    position: absolute; top: 275px; width: 477px; height: 294px;
    box-shadow: 2px 4px 6px rgba(0,0,0,0.45);
  }
  .card-front {
    left: 120px; background: var(--card-white);
    border-radius: 0 52px 0 52px;
  }
  .card-back {
    left: 620px; background: var(--card-black);
    border-radius: 52px 0 52px 0;
  }
  .front-mark {
    position: absolute; left: 62px; top: 122px;
    display: flex; align-items: center; gap: 12px;
    font-weight: 900; font-size: 40px; color: var(--ink); letter-spacing: 1px;
  }
  .mark-square { width: 22px; height: 22px; background: var(--brand-red); }
  .divider {
    position: absolute; left: 238px; top: 87px;
    width: 1px; height: 120px; background: var(--rule);
  }
  .contact { position: absolute; left: 266px; top: 84px; color: var(--ink); }
  .contact-name {
    font-weight: 700; font-size: 16px; color: var(--brand-red);
    letter-spacing: 0.3px; line-height: 18px;
  }
  .contact-role { font-size: 13px; line-height: 15px; margin-bottom: 4px; }
  .contact-line {
    display: flex; align-items: center; gap: 5px;
    font-size: 13.5px; line-height: 18px;
  }
  .contact-line svg { width: 11px; height: 11px; fill: var(--brand-red); flex: none; }
  .contact-address { font-size: 13.5px; line-height: 18px; margin-top: 2px; }
  .back-mark {
    position: absolute; left: 0; right: 0; top: 0; bottom: 0;
    display: flex; align-items: center; justify-content: center; gap: 14px;
    font-weight: 700; font-size: 34px; color: var(--card-white); letter-spacing: 1px;
  }
  .back-mark .mark-square { width: 26px; height: 26px; }
</style>
</head>
<body>
<main class="stage">
  <section class="card card-front" aria-label="Business card front">
    <div class="front-mark"><span class="mark-square"></span><span>KBT</span></div>
    <div class="divider"></div>
    <div class="contact">
      <p class="contact-name">DORAN KELBRATH</p>
      <p class="contact-role">Partner</p>
      <p class="contact-line">
        <svg viewBox="0 0 12 12" aria-hidden="true"><path d="M1 4c0-1.5 2-2.5 5-2.5S11 2.5 11 4v1H8.5V3.8h-5V5H1zM2.5 6h7l1 4.5h-9z"/></svg>
        <span>0461 738 524</span>
      </p>
      <p class="contact-line">
        <svg viewBox="0 0 12 12" aria-hidden="true"><path d="M1 2.5h10v7H1z M1.5 3l4.5 3.5L10.5 3" stroke="#fff" stroke-width="1"/></svg>
        <span>doran@kbtlaw.co</span>
      </p>
      <p class="contact-line">
        <svg viewBox="0 0 12 12" aria-hidden="true"><circle cx="6" cy="6" r="5.5"/><path d="M3 5c1.5-1 2 .5 3 0s1-2 2.5-1.5M4 8.5c1-.8 2.5-.3 3.5.5" stroke="#fff" stroke-width="0.9" fill="none"/></svg>
        <span>www.kbtlaw.co</span>
      </p>
      <p class="contact-address">Level 3, 118 Wendmore<br>Street, Sydney NSW 2000</p>
    </div>
  </section>
  <section class="card card-back" aria-label="Business card back">
    <div class="back-mark"><span class="mark-square"></span><span>KBT LEGAL</span></div>
  </section>
</main>
</body>
</html>
```